Copperleaf Roofing Business Card

This is my current business card. But I’d like to make some changes. Somewhere on the card I’d like to list some of the services we offer. Maybe on the back? But I’d still like to keep the red. White and black modern look.

-residential & commercial roofing
-Roof Repairs & Maintenance
-Storm Damage & Insurance Claims specialist
-Christmas Lights and permanent Christmas lights
Fencing. Windows. Gutters. Siding. Sheetrock, painting.

```html
<!DOCTYPE html>
<html lang="en">
<head>
<meta charset="utf-8">
<title>Copperleaf Roofing Co. – Business Card</title>
<link href="https://fonts.googleapis.com/css2?family=Poppins:wght@400;500;600;700&family=Orbitron:wght@800&display=swap" rel="stylesheet">
<style>
  :root {
    --bg: #dfe3e5;
    --red: #ec1f27;
    --ink: #1a1a1a;
    --card-dark: #19191a;
    --white: #ffffff;
  }
  * { box-sizing: border-box; margin: 0; padding: 0; }
  html, body { width: 1200px; height: 960px; overflow: hidden; }
  body {
    background: var(--bg);
    font-family: "Poppins", Arial, sans-serif;
    position: relative;
  }
  .card {
    position: absolute;
    width: 704px;
    height: 402px;
    border-radius: 30px;
    overflow: hidden;
  }

  /* Front */
  .card-front {
    left: 247px; top: 58px;
    background: var(--white);
    text-align: center;
    color: var(--ink);
  }
  .brand-mark {
    position: absolute;
    border-radius: 50%;
    background: var(--red);
  }
  .card-front .brand-mark {
    left: 299px; top: 44px;
    width: 106px; height: 106px;
  }
  .brand-name {
    position: absolute;
    font-weight: 700;
    text-transform: uppercase;
    line-height: 1;
    text-align: center;
  }
  .brand-name .line-1 { display: block; font-size: 31px; letter-spacing: 1px; color: var(--red); }
  .brand-name .line-2 { display: block; font-size: 21px; letter-spacing: 2px; margin-top: 4px; }
  .card-front .brand-name { left: 0; right: 0; top: 162px; }
  .card-front .brand-name .line-2 { color: var(--ink); }

  .services {
    position: absolute;
    left: 0; right: 0; top: 244px;
  }
  .services-title {
    color: var(--red);
    font-weight: 600;
    font-size: 16px;
    letter-spacing: 0.5px;
    line-height: 22px;
  }
  .services-list { list-style: none; }
  .services-list li {
    font-size: 16.5px;
    line-height: 23px;
    letter-spacing: 0.3px;
  }

  /* Back */
  .card-back {
    left: 250px; top: 500px;
    background: var(--card-dark);
    color: var(--white);
  }
  .card-back .brand-mark {
    left: 77px; top: 27px;
    width: 110px; height: 110px;
  }
  .card-back .brand-name {
    left: 0; width: 264px;
    top: 146px;
  }
  .card-back .brand-name .line-2 { color: var(--white); }

  .holder {
    position: absolute;
    right: 32px; top: 33px;
    text-align: right;
  }
  .holder-name {
    font-family: "Orbitron", "Poppins", sans-serif;
    font-weight: 800;
    font-size: 32px;
    letter-spacing: 1.5px;
    line-height: 1;
  }
  .holder-name .first { color: var(--red); margin-right: 12px; }
  .holder-role {
    font-weight: 600;
    font-size: 17px;
    letter-spacing: 0.5px;
    line-height: 1;
    margin-top: 11px;
  }
  .accent-bar {
    position: absolute;
    right: 0; top: 32px;
    width: 19px; height: 54px;
    background: var(--red);
  }

  .contact-band {
    position: absolute;
    left: 0; right: 0; bottom: 0;
    height: 104px;
    background: var(--red);
  }
  .contact-list {
    list-style: none;
    position: absolute;
    left: 23px; top: 9px;
  }
  .contact-list li {
    display: flex;
    align-items: center;
    font-size: 18.5px;
    line-height: 23px;
    letter-spacing: 0.3px;
  }
  .contact-list svg { width: 15px; height: 15px; margin-right: 10px; flex: none; }
  .corner-mark {
    position: absolute;
    right: 11px; bottom: 1px;
    width: 102px; height: 102px;
    border-radius: 50%;
    background: var(--card-dark);
    border: 3px solid var(--white);
  }
</style>
</head>
<body>

  <section class="card card-front" aria-label="Card front">
    <div class="brand-mark" aria-hidden="true"></div>
    <div class="brand-name">
      <span class="line-1">Copperleaf</span>
      <span class="line-2">Roofing Co.</span>
    </div>
    <div class="services">
      <h2 class="services-title">SERVICES WE OFFER</h2>
      <ul class="services-list">
        <li>Roof Repairs &amp; Maintenance</li>
        <li>Residential &amp; Commercial Roofing</li>
        <li>Storm Damage &amp; Insurance Claims Specialist</li>
        <li>Christmas Lights and Permanent Christmas lights</li>
        <li>Fencing. Windows. Gutters. Siding. Sheetrock, Painting</li>
      </ul>
    </div>
  </section>

  <section class="card card-back" aria-label="Card back">
    <div class="brand-mark" aria-hidden="true"></div>
    <div class="brand-name">
      <span class="line-1">Copperleaf</span>
      <span class="line-2">Roofing Co.</span>
    </div>

    <div class="holder">
      <div class="holder-name"><span class="first">DANE</span>MARSH</div>
      <div class="holder-role">OWNER</div>
    </div>
    <div class="accent-bar"></div>

    <div class="contact-band">
      <ul class="contact-list">
        <li>
          <svg viewBox="0 0 24 24" fill="#fff" aria-hidden="true"><path d="M6.6 10.8a15.1 15.1 0 0 0 6.6 6.6l2.2-2.2a1 1 0 0 1 1-.25 11.4 11.4 0 0 0 3.6.57 1 1 0 0 1 1 1V20a1 1 0 0 1-1 1A17 17 0 0 1 3 4a1 1 0 0 1 1-1h3.5a1 1 0 0 1 1 1c0 1.25.2 2.45.57 3.57a1 1 0 0 1-.25 1z"/></svg>
          682-555-0148
        </li>
        <li>
          <svg viewBox="0 0 24 24" fill="none" stroke="#fff" stroke-width="2" aria-hidden="true"><circle cx="12" cy="12" r="10"/><path d="M2 12h20M12 2c3 3.5 3 16.5 0 20M12 2c-3 3.5-3 16.5 0 20"/></svg>
          www.copperleafroofing.co
        </li>
        <li>
          <svg viewBox="0 0 24 24" fill="none" stroke="#fff" stroke-width="2" aria-hidden="true"><rect x="2" y="5" width="20" height="15" rx="1"/><path d="M2 6l10 8 10-8"/></svg>
          Dane@copperleafroofing.co
        </li>
      </ul>
    </div>
    <div class="corner-mark" role="img" aria-label="Company emblem"></div>
  </section>

</body>
</html>
```